Business card design needed

i am a manufacturer of rocky road chocolate bars. my company is called velvet crag confections p/l , trading as aunty pearls delights which we call our rocky road aunty pearls crunch slab. we also retail lollies under the aunty pearls delights name from a shop front.our colours on the logo are burgandy and gold higlights.

Target Market(s)

retail and wholesale

Industry/Entity Type

Retail

Requirements
Must have
• company name and trading as name address phone numbers
velvet crag confections
t/a aunty pearls delights
14 wexton st
brixley victoria 3187
tel 03 9481 5527
marlene mobile 0417 538291
desmond mobile 0428 615 903
the designer can place the names and numbers where he/she thinks it would be appropriate.

```html
<!DOCTYPE html>
<html lang="en">
<head>
<meta charset="utf-8">
<title>Aunty Pearls Delights – Business Card</title>
<link rel="stylesheet" href="https://fonts.googleapis.com/css2?family=Bitter:wght@400;700&display=swap">
<style>
  :root {
    --burgundy: #8e1f56;
    --gold-light: #fbe6a6;
    --gold: #f2b548;
    --gold-deep: #d98f1c;
    --cream: #f5f1e4;
    --ink: #2e2a26;
    --backdrop: #e7e3dc;
  }
  * { box-sizing: border-box; margin: 0; padding: 0; }
  html, body {
    width: 1200px;
    height: 787px;
    overflow: hidden;
    background: var(--backdrop);
    font-family: "Bitter", Georgia, serif;
  }
  .card-set {
    display: flex;
    gap: 48px;
    justify-content: center;
    align-items: center;
    width: 1200px;
    height: 787px;
  }
  .card {
    position: relative;
    width: 525px;
    height: 300px;
    border-radius: 3px;
    box-shadow: 0 6px 18px rgba(60, 40, 20, 0.22);
    overflow: hidden;
  }

  /* Contact side */
  .card--contact {
    background: var(--cream);
  }
  .card__band {
    position: absolute;
    left: 0;
    right: 0;
    height: 18px;
    background: var(--burgundy);
  }
  .card__band--top { top: 0; }
  .card__band--bottom { bottom: 0; }
  .contact {
    position: absolute;
    top: 46px;
    right: 48px;
    text-align: right;
  }
  .contact__company,
  .contact__trading {
    color: var(--burgundy);
    font-weight: 700;
    font-size: 20px;
    line-height: 1.2;
  }
  .contact__trading {
    margin-bottom: 18px;
  }
  .contact__line {
    color: var(--ink);
    font-size: 15px;
    line-height: 1.6;
  }

  /* Brand side */
  .card--brand {
    background: radial-gradient(ellipse at 50% 45%, var(--gold-light) 0%, var(--gold) 62%, var(--gold-deep) 100%);
    display: flex;
    align-items: center;
    justify-content: center;
  }
  .brand {
    display: flex;
    align-items: center;
    gap: 16px;
  }
  .brand__dot {
    width: 26px;
    height: 26px;
    border-radius: 50%;
    background: var(--burgundy);
  }
  .brand__name {
    color: var(--burgundy);
    font-weight: 700;
    font-size: 34px;
    line-height: 1.15;
  }
</style>
</head>
<body>
  <main class="card-set">
    <section class="card card--contact" aria-label="Contact side">
      <div class="card__band card__band--top"></div>
      <div class="contact">
        <p class="contact__company">Velvet Crag Confections</p>
        <p class="contact__trading">t/a Aunty Pearls Delights</p>
        <p class="contact__line">14 Wexton St</p>
        <p class="contact__line">Brixley Victoria 3187</p>
        <p class="contact__line">tel: 03 9481 5527</p>
        <p class="contact__line">mobile: 0417 538291 (Marlene)</p>
        <p class="contact__line">mobile: 0428 615 903 (Desmond)</p>
      </div>
      <div class="card__band card__band--bottom"></div>
    </section>

    <section class="card card--brand" aria-label="Brand side">
      <div class="brand">
        <span class="brand__dot"></span>
        <p class="brand__name">Aunty Pearls<br>Crunch Slab</p>
      </div>
    </section>
  </main>
</body>
</html>
```